BOLD & MINIMALIST DESIGN NEEDED

We want a very bold but minimalistic business card design that is impactful and utilizes both sides of the business card. Our current logo is included for your use.

We want bold fonts and good use of negative space. We don't want the logo to overpower the design.

Target Market(s)

Professionals who are building new commercial buildings.

Industry/Entity Type

Construction

Contact Information for Business Card

Name, Title, email, office phone, cell phone, website

Font styles to use
Serif
Sans Serif

Requirements
Must have
• Bold design!

```html
<!DOCTYPE html>
<html lang="en">
<head>
<meta charset="utf-8">
<title>Ridgecrest Business Card</title>
<link href="https://fonts.googleapis.com/css2?family=Arimo:wght@400;700&display=swap" rel="stylesheet">
<style>
  :root {
    --page: #e6e6e6;
    --paper: #ffffff;
    --ink: #111111;
    --text: #555555;
    --green: #7cc22e;
    --green-deep: #8cc63f;
    --green-light: #b9df86;
    --rule: #333333;
  }
  * { box-sizing: border-box; margin: 0; padding: 0; }
  html, body {
    width: 1200px; height: 1200px; overflow: hidden;
    background: var(--page);
    font-family: "Arimo", Arial, sans-serif;
  }
  .canvas { position: relative; width: 1200px; height: 1200px; }
  .card {
    position: absolute;
    width: 688px; height: 393px;
  }
  .card--front { left: 267px; top: 159px; background: var(--paper); }
  .card--back {
    left: 262px; top: 653px;
    background: radial-gradient(ellipse 55% 60% at 50% 42%, var(--green-light) 0%, var(--green-deep) 100%);
  }
  .holder { position: absolute; left: 0; right: 0; top: 52px; text-align: center; }
  .holder__name { font-weight: 700; font-size: 26px; color: var(--ink); letter-spacing: 0.5px; line-height: 1; }
  .holder__title { margin-top: 6px; font-size: 15px; color: var(--green); }
  .rule { position: absolute; left: 46px; width: 594px; height: 1px; background: var(--rule); }
  .rule--top { top: 133px; }
  .rule--mid { top: 228px; }
  .info { position: absolute; font-size: 16px; color: var(--text); line-height: 21px; white-space: nowrap; }
  .label { color: var(--green); font-weight: 700; }
  .info--address { left: 46px; top: 142px; }
  .info--tel { left: 46px; top: 198px; }
  .info--cell { right: 46px; top: 198px; }
  .info--email { left: 46px; top: 239px; }
  .web {
    position: absolute; left: 46px; top: 322px;
    font-size: 16px; font-weight: 700; letter-spacing: 3.6px; color: #444;
  }
  .web__domain { color: var(--green); }
  .brand-small {
    position: absolute; right: 48px; top: 300px;
    display: flex; align-items: center; gap: 7px;
    font-weight: 700; font-size: 22px; color: var(--ink);
  }
  .brand-small__mark { width: 14px; height: 14px; background: var(--ink); }
  .brand-large {
    position: absolute; left: 0; right: 0; top: 160px;
    display: flex; justify-content: center; align-items: center; gap: 18px;
    font-weight: 700; font-size: 62px; color: var(--ink); letter-spacing: 1px;
  }
  .brand-large__mark { width: 40px; height: 40px; background: var(--ink); }
</style>
</head>
<body>
<main class="canvas">
  <section class="card card--front" aria-label="Card front">
    <header class="holder">
      <h1 class="holder__name">DANIEL MOORE</h1>
      <p class="holder__title">President</p>
    </header>
    <div class="rule rule--top"></div>
    <p class="info info--address"><span class="label">Address :</span> 4412 Alder Court<br>Fairview, Canada 58210</p>
    <p class="info info--tel"><span class="label">Tel :</span> 555-214-8630</p>
    <p class="info info--cell"><span class="label">Cell :</span> 555-390-7142</p>
    <div class="rule rule--mid"></div>
    <p class="info info--email"><span class="label">Email :</span> info@ridgecrest.com</p>
    <p class="web">www.<span class="web__domain">ridgecrest</span>.com</p>
    <div class="brand-small"><span class="brand-small__mark"></span>RIDGECREST</div>
  </section>
  <section class="card card--back" aria-label="Card back">
    <div class="brand-large"><span class="brand-large__mark"></span>RIDGECREST</div>
  </section>
</main>
</body>
</html>
```